Tandem Hearth Works Pty Ltd

We need business cards for a company based in Perth, we install, service and maintain fire equipment.
On the front we want a great design with our logo and a small spot for our full company name, general company email address and office number. On the back we need space for our name, title, mobile number and email address on the back.

Target Market(s)

Facility managers and commercial/industrial building owners/occupiers.

Contact Information for Business Card

Font styles to use
Sans Serif

Requirements
Must have
• Please only submit 5 of your best samples.
Darker tones are preferred.
Nice to have
• We want to use, black, red and grey. Keep it modern and clean.
I've attached the company logo and a sample of a boarder we use on our emergency plans.
Should not have
• No preference. Let the designer choose.

```html
<!DOCTYPE html>
<html lang="en">
<head>
<meta charset="utf-8">
<title>Tandem Hearth Works – Business Cards</title>
<link href="https://fonts.googleapis.com/css2?family=Arimo:wght@400;700&display=swap" rel="stylesheet">
<style>
  :root {
    --stage: #2a2422;
    --card: #161616;
    --red: #ec1c24;
    --white: #f2f2f2;
    --grey: #8a8a8a;
  }
  * { box-sizing: border-box; margin: 0; padding: 0; }
  html, body { width: 1200px; height: 842px; overflow: hidden; }
  body {
    background: var(--stage);
    font-family: "Arimo", Arial, sans-serif;
    position: relative;
  }
  .card {
    position: absolute;
    top: 266px;
    width: 540px;
    height: 309px;
    background: var(--card);
    overflow: hidden;
    box-shadow: 0 12px 30px rgba(0,0,0,.5);
  }
  .card--personal { left: 40px; }
  .card--company { left: 620px; }

  /* personal side */
  .band { position: absolute; left: 0; width: 100%; height: 14px; background: var(--red); }
  .band--top { top: 0; }
  .band--bottom { bottom: 0; }
  .brand-name {
    position: absolute; top: 62px; width: 100%; text-align: center;
    color: var(--red); font-weight: 700; font-size: 38px; letter-spacing: 1px;
  }
  .person { position: absolute; top: 140px; width: 100%; text-align: center; }
  .person__name { color: var(--red); font-weight: 700; font-size: 24px; letter-spacing: .5px; text-transform: uppercase; }
  .person__title { color: var(--white); font-size: 17px; margin-top: 2px; }
  .divider { width: 160px; height: 1px; background: var(--grey); margin: 12px auto 14px; }
  .contact-row { display: flex; justify-content: center; gap: 22px; color: var(--white); font-size: 17px; }
  .contact { display: flex; align-items: center; gap: 8px; }
  .icon { width: 18px; height: 18px; flex: none; }

  /* company side */
  .tab { position: absolute; width: 26px; height: 50px; background: var(--red); }
  .tab--left { left: 0; top: 168px; }
  .tab--right { right: 0; top: 70px; }
  .company { position: absolute; top: 92px; width: 100%; text-align: center; }
  .company__name { color: var(--red); font-weight: 700; font-size: 20px; line-height: 1.15; text-transform: uppercase; }
  .company__phone { color: var(--white); font-weight: 700; font-size: 26px; margin-top: 8px; }
  .company__links { display: flex; justify-content: center; gap: 18px; color: var(--white); font-size: 13px; margin-top: 10px; }
  .company__links .icon { width: 14px; height: 14px; }
</style>
</head>
<body>
  <section class="card card--personal">
    <div class="band band--top"></div>
    <div class="brand-name">TANDEM HEARTH</div>
    <div class="person">
      <div class="person__name">Marcus Delane</div>
      <div class="person__title">Managing Director</div>
      <div class="divider"></div>
      <div class="contact-row">
        <span class="contact">
          <svg class="icon" viewBox="0 0 18 18"><rect x="4" y="1.5" width="10" height="15" rx="2" fill="none" stroke="#ec1c24" stroke-width="2"/><circle cx="9" cy="13.5" r="1" fill="#ec1c24"/></svg>
          555.0142.7781
        </span>
        <span class="contact">
          <svg class="icon" viewBox="0 0 18 18"><rect x="1" y="4" width="16" height="11" fill="#ec1c24"/><path d="M1 4 L9 10 L17 4" fill="none" stroke="#161616" stroke-width="1.3"/></svg>
          name@tandemhearth.com
        </span>
      </div>
    </div>
    <div class="band band--bottom"></div>
  </section>

  <section class="card card--company">
    <div class="tab tab--right"></div>
    <div class="tab tab--left"></div>
    <div class="company">
      <div class="company__name">Tandem Hearth<br>Works Pty Ltd</div>
      <div class="company__phone">555.0190.2264</div>
      <div class="company__links">
        <span class="contact">
          <svg class="icon" viewBox="0 0 18 18"><rect x="1" y="4" width="16" height="11" fill="#ec1c24"/><path d="M1 4 L9 10 L17 4" fill="none" stroke="#161616" stroke-width="1.3"/></svg>
          info@tandemhearth.com
        </span>
        <span class="contact">
          <svg class="icon" viewBox="0 0 18 18"><circle cx="9" cy="9" r="7.5" fill="none" stroke="#ec1c24" stroke-width="1.6"/><ellipse cx="9" cy="9" rx="3.2" ry="7.5" fill="none" stroke="#ec1c24" stroke-width="1.3"/><path d="M1.5 9 H16.5" stroke="#ec1c24" stroke-width="1.3"/></svg>
          www.tandemhearth.com
        </span>
      </div>
    </div>
  </section>
</body>
</html>
```